Webshop Template

For our Webstore in UK we need a complete Template,
shoppingcart is Magento, the Shop is focussed on Download software,

the name: Kelvoramarket.co.uk

Check out some other good stores, like zandrilo.de
Updates

for example the Page from 

www.brunt.co.uk or

www.zandrilo.de

www.mokvelta.de

www.quarnepreis.de

The Logodesign which are in Consideration

http://www.plimvector.com/design/5520913/logo-design-by-tomek7ga

http://www.plimvector.com/design/5518207/logo-design-by-ivanoralba

http://www.plimvector.com/design/5517346/logo-design-by-granite-fables

http://www.plimvector.com/design/5516085/logo-design-by-quillotaste

http://www.plimvector.com/design/5515472/logo-design-by-tuvaro

http://www.plimvector.com/design/5514619/logo-design-by-lone-pine-graphic-

Target Market(s)

B2C - Consumer Marcet

Industry/Entity Type

Shop

```html
<!DOCTYPE html>
<html lang="en">
<head>
<meta charset="utf-8">
<title>Kelvora Market – Webshop Template</title>
<link href="https://fonts.googleapis.com/css2?family=Arimo:ital,wght@0,400;0,700;1,400;1,700&family=Cabin:ital,wght@1,600;1,700&family=Dancing+Script:wght@500&display=swap" rel="stylesheet">
<style>
  :root{
    --navy:#1d4f8c;
    --blue:#2f7fc4;
    --sky:#4a9ad6;
    --link:#2b66a8;
    --red:#c8161b;
    --orange:#f39a0c;
    --orange-dark:#e07a00;
    --text:#555;
    --muted:#777;
    --line:#d9d9d9;
    --panel:#f2f2f2;
    --white:#fff;
  }
  *{box-sizing:border-box;margin:0;padding:0}
  html,body{width:911px;height:1200px;overflow:hidden;background:var(--white)}
  body{font-family:"Arimo",Arial,sans-serif;color:var(--text);font-size:8px}
  .canvas{position:relative;width:911px;height:1200px;overflow:hidden}
  .abs{position:absolute}

  /* header */
  .brand{left:137px;top:12px;display:flex;align-items:center;gap:8px}
  .brand-dot{width:30px;height:30px;border-radius:50%;background:var(--blue)}
  .brand-name{font-size:21px;font-weight:700;color:var(--navy);letter-spacing:-.3px}
  .top-links{right:137px;top:17px;font-size:7px;color:var(--navy);display:flex;gap:14px}
  .search{left:432px;top:47px;width:198px;height:14px;border:1px solid #cfcfcf;display:flex}
  .search span{flex:1;font-size:6.5px;color:#777;padding:3px 6px 0 19px;position:relative}
  .search span::before{content:"";position:absolute;left:6px;top:3px;width:6px;height:6px;border:1px solid #888;border-radius:50%}
  .search b{width:37px;background:#6b6b6b;color:#eee;font-weight:400;font-size:6.5px;text-align:center;line-height:13px}
  .cart{left:644px;top:34px;width:129px;height:29px;border:1px solid #ddd;display:flex;align-items:center;gap:7px;padding-left:10px;font-size:8px;color:var(--navy)}
  .cart i{width:18px;height:12px;background:#7aa33a;border-radius:2px}
  .cart em{font-style:normal;color:var(--red)}

  /* nav */
  .nav{left:137px;top:73px;width:637px;height:21px;background:linear-gradient(#fafafa,#e8e8e8);border:1px solid #e0e0e0;display:flex;font-size:8px;color:#555}
  .nav a{padding:0 18px;line-height:20px}
  .nav a.active{background:var(--sky);color:#fff;margin-left:7px;padding:0 13px}

  /* hero */
  .hero{left:137px;top:106px;width:436px;height:216px;overflow:hidden;background:linear-gradient(#d9e8f5,#8fb6dd)}
  .hero-dark{position:absolute;inset:0;background:linear-gradient(135deg,#2e66a8,#163f7e);clip-path:polygon(62% 0,100% 0,100% 100%,34% 100%)}
  .hero-title{left:18px;top:30px;font-family:"Cabin",sans-serif;font-style:italic;font-weight:700;font-size:17px;line-height:22px;color:var(--navy)}
  .hero-copy{left:19px;top:100px;width:110px;font-size:6.5px;line-height:12px;color:#333}
  .hero-free{left:17px;top:139px;font-family:"Cabin",sans-serif;font-style:italic;font-weight:700;font-size:15px;color:var(--red)}
  .btn{background:linear-gradient(#fcb532,var(--orange-dark));color:#fff;text-align:center;border:1px solid #d97400}
  .hero-dl{left:15px;top:163px;width:102px;height:29px;font-family:"Cabin",sans-serif;font-style:italic;font-weight:700;font-size:15px;line-height:27px}
  .hero-brand{left:183px;top:82px;font-family:"Cabin",sans-serif;font-style:italic;font-weight:700;font-size:16px;line-height:24px;color:#fff}
  .hero-offer{left:180px;top:138px;font-family:"Cabin",sans-serif;font-style:italic;font-weight:700;color:var(--orange);font-size:15px;line-height:21px}
  .hero-offer b{font-size:20px;display:block}
  .hero-seal{left:276px;top:5px;width:56px;height:56px;border-radius:50%;background:radial-gradient(#e33a1e,#b8160e);border:3px solid #f6c21a;color:#fff;text-align:center;font-family:"Cabin",sans-serif;font-style:italic;font-weight:700;font-size:15px;line-height:16px;padding-top:11px}
  .hero-seal small{display:block;font-size:8px;line-height:9px;color:#f6d24a}
  .hero-pc{left:240px;top:52px;width:190px;height:158px;background:radial-gradient(circle at 60% 45%,#5aa9e6,#1a2b45 55%,transparent 75%)}

  /* welcome box */
  .welcome{left:585px;top:106px;width:189px;height:110px;background:linear-gradient(#f6f6f6,#fff);border:1px solid #eee;padding:14px 15px}
  .welcome h3{font-weight:400;font-size:11px;color:var(--navy)}
  .welcome h2{font-weight:400;font-size:16px;color:var(--red);margin:2px 0 4px}
  .welcome p{font-size:6.5px;line-height:12px;color:#666}
  .btn-blue{background:linear-gradient(#3d8fd3,#2469ae);color:#fff;font-size:9px;text-align:center;line-height:19px;height:19px;top:80px}
  .b-login{left:20px;width:68px}
  .b-signup{left:100px;width:67px}

  /* shipping box */
  .ship{left:585px;top:229px;width:189px;height:93px;background:linear-gradient(#5aa7e0,#2f83c6);overflow:hidden}
  .ship-photo{right:0;top:0;width:90px;height:93px;background:linear-gradient(#e9edf1,#c9d6df)}
  .ship h4{left:12px;top:10px;font-weight:400;font-size:8.5px;color:#fff}
  .ship p{left:12px;top:24px;font-family:"Cabin",sans-serif;font-style:italic;font-weight:700;font-size:11px;line-height:14px;color:#f6d12a}
  .ship p small{font-size:9px}
  .ship .btn{left:13px;top:60px;width:67px;height:16px;font-size:8px;font-style:italic;line-height:14px}

  /* partners */
  .partners{left:137px;top:332px;width:637px;height:50px;border:1px solid #ddd;display:flex;justify-content:space-around;align-items:center}
  .partner{display:flex;align-items:center;gap:5px;font-size:13px;color:#555}
  .partner i{width:14px;height:14px;border-radius:50%;background:#9aa6b2}

  /* main */
  .intro{left:137px;top:394px;width:443px}
  .intro h1{font-weight:400;font-size:12px;color:var(--navy);margin-bottom:6px}
  .intro p{font-size:6.5px;line-height:12.5px;color:#666}
  .label{left:139px;font-size:8px;color:var(--navy)}
  .shelf{left:137px;width:443px;height:160px;border:1px solid var(--line);background:linear-gradient(#fff,#ececec);display:grid;grid-template-columns:repeat(4,1fr);padding:0 3px}
  .item{position:relative;text-align:center}
  .item .shot{position:absolute;left:26px;top:11px;width:54px;height:62px;border-radius:2px}
  .item p{position:absolute;left:0;right:0;top:75px;font-size:7px;line-height:12px;color:var(--link)}
  .item .price{position:absolute;left:0;right:0;top:114px;font-size:13px;color:var(--red)}
  .item .btn{position:absolute;left:26px;top:133px;width:54px;height:14px;font-size:7px;font-style:italic;line-height:12px}
  .s1{background:linear-gradient(135deg,#3b7fd0,#bfe0f7)}
  .s2{background:linear-gradient(135deg,#f2c02a,#222)}
  .s3{background:linear-gradient(135deg,#2f9a3c,#8fd45d)}
  .s4{background:linear-gradient(135deg,#1e66c6,#f0a11e)}
  .s5{background:linear-gradient(135deg,#f07a1a,#fde2b8)}
  .s6{background:linear-gradient(135deg,#f3d21f,#d4221c)}
  .s7{background:linear-gradient(135deg,#3f9c33,#e8ead8)}
  .s8{background:linear-gradient(135deg,#8a4cc2,#e8b53a)}
  .s9{background:linear-gradient(135deg,#1d56b0,#48c24a)}
  .s10{background:linear-gradient(135deg,#101d44,#3f8be0)}
  .s11{background:linear-gradient(135deg,#1f62b8,#9cc9ee)}
  .s12{background:linear-gradient(135deg,#1b1b1b,#3a7fd0)}

  /* sidebar */
  .featured{left:596px;top:398px;width:178px;border:1px solid var(--line)}
  .featured h4{background:linear-gradient(#5da6df,#3689cb);color:#fff;font-weight:400;font-size:8px;padding:4px 14px;height:18px}
  .featured li{list-style:none;height:19.6px;border-top:1px solid #e4e4e4;font-size:6.5px;color:#333;line-height:19px;padding-left:23px;position:relative}
  .featured li::before{content:"";position:absolute;left:10px;top:6px;border:4px solid transparent;border-top:6px solid var(--sky)}
  .news{left:601px;top:627px;width:172px}
  .news h4{font-weight:400;font-size:9.5px;color:var(--navy);margin-bottom:6px}
  .news p{font-size:6.5px;line-height:12.5px;color:#666}
  .news-input{left:599px;top:674px;width:175px;height:15px;border:1px solid #ccc;font-size:6.5px;color:#999;padding:4px 7px}
  .news-btn{left:708px;top:696px;width:66px;height:19px;font-size:8px;font-style:italic;line-height:17px}
  .offer{left:596px;top:727px;width:178px;height:271px;border:1px solid var(--line);text-align:center}
  .offer h3{margin-top:10px;font-family:"Cabin",sans-serif;font-style:italic;font-weight:700;font-size:15px;color:var(--navy)}
  .offer .kicker{font-size:9.5px;color:var(--orange-dark);margin-top:4px}
  .offer-shot{left:13px;top:55px;width:152px;height:105px;background:linear-gradient(135deg,#3c9a2e,#a5dc4b 55%,#d8f0a6)}
  .offer .k2{left:0;right:0;top:189px}
  .offer .desc{left:13px;top:205px;width:150px;text-align:left;font-size:7px;line-height:14px;color:var(--link)}
  .offer .cost{left:16px;top:240px;font-size:14px;color:var(--red)}
  .offer .btn{left:90px;top:237px;width:76px;height:22px;font-size:9.5px;font-style:italic;line-height:20px}

  /* social & trust */
  .social{left:137px;top:1014px;width:637px;height:50px;background:linear-gradient(#e6e6e6,#fff 30%);display:flex;align-items:center;padding-left:21px}
  .social .script{font-family:"Dancing Script",cursive;font-size:14px;color:var(--orange-dark);margin-right:8px}
  .social i{width:23px;height:23px;border-radius:4px;background:linear-gradient(#5c8fd6,#2d5aa8);margin-right:6px}
  .trust{display:flex;gap:8px;margin-left:16px;align-items:center}
  .trust i{display:block;border-radius:2px;background:#c7ccd3}
  .trust .w{width:30px;height:14px}
  .trust .c{width:22px;height:13px;background:#dfe3e8;border:1px solid #c8ccd2}

  /* footer */
  .footer{left:137px;top:1072px;width:637px;height:98px;background:var(--panel);padding:13px 0 0 18px;display:grid;grid-template-columns:124px 124px 131px 124px 1fr}
  .footer h5{font-weight:400;font-size:9px;color:var(--navy);margin-bottom:5px}
  .footer li{list-style:none;font-size:6px;line-height:12.3px;color:#555;text-transform:uppercase}
  .copy{left:139px;top:1180px;font-size:6px;color:#666}
  .copy em{font-style:normal;color:var(--blue)}
</style>
</head>
<body>
<div class="canvas">

  <!-- header -->
  <div class="abs brand"><i class="brand-dot"></i><span class="brand-name">Kelvora Market</span></div>
  <div class="abs top-links"><span>My Account</span><span>|</span><span>My Cart</span><span>|</span><span>Login</span></div>
  <div class="abs search"><span>Search entire store here</span><b>SEARCH</b></div>
  <div class="abs cart"><i></i>Your Cart is : <em>0 Items</em></div>

  <nav class="abs nav">
    <a class="active">Home</a><a>Software</a><a>Products</a><a>Services</a><a>Contact us</a>
  </nav>

  <!-- hero banner -->
  <section class="abs hero">
    <div class="hero-dark"></div>
    <div class="abs hero-pc" role="img" aria-label="Desktop computer with monitor, keyboard and mouse"></div>
    <div class="abs hero-title">OUR<br>SOFTWARE<br>DOWNLOADS</div>
    <p class="abs hero-copy">Lorem Ipsum is simply dummy text of the printing and typeset-ting industry.</p>
    <div class="abs hero-free">Free Trial</div>
    <div class="abs btn hero-dl">Download</div>
    <div class="abs hero-brand">Kelvora<br>Market</div>
    <div class="abs hero-offer">20%<b>Offer</b></div>
    <div class="abs hero-seal">Free<small>Trail</small></div>
  </section>

  <!-- welcome -->
  <section class="abs welcome">
    <h3>Welcome to</h3>
    <h2>Kelvora Market</h2>
    <p>Lorem Ipsum is simply dummy text of the printing and typesetting industry.</p>
    <div class="abs btn-blue b-login">LOGIN</div>
    <div class="abs btn-blue b-signup">SIGNUP</div>
  </section>

  <!-- shipping -->
  <section class="abs ship">
    <div class="abs ship-photo" role="img" aria-label="Photo of a shopper holding a sign reading Save your money"></div>
    <h4 class="abs">FREE SHIPPING</h4>
    <p class="abs">Lorem Ipsum is<br><small>simply dummy</small></p>
    <div class="abs btn">Click Here</div>
  </section>

  <!-- partners -->
  <section class="abs partners">
    <span class="partner"><i></i>Pelvaro</span>
    <span class="partner"><i></i>Quintell</span>
    <span class="partner"><i></i>Morvisk</span>
    <span class="partner"><i></i>Tandrel</span>
    <span class="partner"><i></i>Oskerlund</span>
  </section>

  <!-- intro -->
  <section class="abs intro">
    <h1>Welcome to Kelvora Market</h1>
    <p>Lorem Ipsum is simply dummy text of the printing and typesetting industry. Lorem Ipsum has been the industry's standard dummy text ever since the 1500s,Lorem Ipsum is simply dummy text of the printing and typesetting industry.</p>
  </section>

  <div class="abs label" style="top:447px">OUR PRODUCTS</div>
  <section class="abs shelf" style="top:462px">
    <div class="item"><div class="shot s1" role="img" aria-label="Software box"></div><p>Lorem Ipsum is<br>simply dummy text<br>of the printing</p><div class="price">$289.99</div><div class="btn">Click Here</div></div>
    <div class="item"><div class="shot s2" role="img" aria-label="Operating system boxes"></div><p>Lorem Ipsum is<br>simply dummy text<br>of the printing</p><div class="price">$289.99</div><div class="btn">Click Here</div></div>
    <div class="item"><div class="shot s3" role="img" aria-label="Software box"></div><p>Lorem Ipsum is<br>simply dummy text<br>of the printing</p><div class="price">$289.99</div><div class="btn">Click Here</div></div>
    <div class="item"><div class="shot s4" role="img" aria-label="Software box"></div><p>Lorem Ipsum is<br>simply dummy text<br>of the printing</p><div class="price">$289.99</div><div class="btn">Click Here</div></div>
  </section>

  <div class="abs label" style="top:636px">RECENT PRODUCTS</div>
  <section class="abs shelf" style="top:651px">
    <div class="item"><div class="shot s5" role="img" aria-label="Software box"></div><p>Lorem Ipsum is<br>simply dummy text<br>of the printing</p><div class="price">$289.99</div><div class="btn">Click Here</div></div>
    <div class="item"><div class="shot s6" role="img" aria-label="Software box"></div><p>Lorem Ipsum is<br>simply dummy text<br>of the printing</p><div class="price">$289.99</div><div class="btn">Click Here</div></div>
    <div class="item"><div class="shot s7" role="img" aria-label="Software box"></div><p>Lorem Ipsum is<br>simply dummy text<br>of the printing</p><div class="price">$289.99</div><div class="btn">Click Here</div></div>
    <div class="item"><div class="shot s8" role="img" aria-label="Software box"></div><p>Lorem Ipsum is<br>simply dummy text<br>of the printing</p><div class="price">$289.99</div><div class="btn">Click Here</div></div>
  </section>

  <div class="abs label" style="top:822px">MORE FEATURED DEALS</div>
  <section class="abs shelf" style="top:838px">
    <div class="item"><div class="shot s9" role="img" aria-label="Software box"></div><p>Lorem Ipsum is<br>simply dummy text<br>of the printing</p><div class="price">$289.99</div><div class="btn">Click Here</div></div>
    <div class="item"><div class="shot s10" role="img" aria-label="Software box"></div><p>Lorem Ipsum is<br>simply dummy text<br>of the printing</p><div class="price">$289.99</div><div class="btn">Click Here</div></div>
    <div class="item"><div class="shot s11" role="img" aria-label="Software box"></div><p>Lorem Ipsum is<br>simply dummy text<br>of the printing</p><div class="price">$289.99</div><div class="btn">Click Here</div></div>
    <div class="item"><div class="shot s12" role="img" aria-label="Software box"></div><p>Lorem Ipsum is<br>simply dummy text<br>of the printing</p><div class="price">$289.99</div><div class="btn">Click Here</div></div>
  </section>

  <!-- sidebar -->
  <aside class="abs featured">
    <h4>FEATURED STORES</h4>
    <ul>
      <li>Lorem Ipsum is simply dummy</li>
      <li>Lorem Ipsum is simply</li>
      <li>Lorem Ipsum is simply dummy</li>
      <li>Lorem Ipsum is simply dummy simply dummy</li>
      <li>Lorem Ipsum</li>
      <li>Lorem Ipsum is simply dummy</li>
      <li>Lorem Ipsum is simply dummy dummy</li>
      <li>Lorem Ipsum is simply dummy</li>
      <li>Lorem Ipsum</li>
      <li>Lorem Ipsum is simply dummy</li>
    </ul>
  </aside>

  <section class="abs news">
    <h4>NEWSLETTER</h4>
    <p>Lorem Ipsum is simply dummy text of the printing and typesetting industry.</p>
  </section>
  <div class="abs news-input">Enter your Email ID :</div>
  <div class="abs btn news-btn">Click Here</div>

  <section class="abs offer">
    <h3>Offer Products</h3>
    <div class="kicker">LOREM IPSUM IS SIMPLY</div>
    <div class="abs offer-shot" role="img" aria-label="Green game backup software box with disc and price seal 9.75$ for sale"></div>
    <div class="abs kicker k2">LOREM IPSUM IS SIMPLY</div>
    <p class="abs desc">Lorem Ipsum is simply dummy text of the printing and typesetting industry.</p>
    <div class="abs cost">$ 160.00</div>
    <div class="abs btn">Click Here</div>
  </section>

  <!-- social & trust -->
  <section class="abs social">
    <span class="script">Connect to Our Social Network :</span>
    <i></i><i></i><i></i><i></i>
    <div class="trust">
      <i class="w"></i><i class="w"></i><i class="w"></i><i class="w" style="width:40px"></i>
      <i class="c"></i><i class="c"></i><i class="c"></i><i class="c"></i><i class="c"></i>
    </div>
  </section>

  <!-- footer -->
  <footer class="abs footer">
    <div><h5>HELP</h5><ul><li>Payments</li><li>Saved Cards</li><li>Shipping Cancellation</li><li>Returns</li><li>FAQ</li></ul></div>
    <div><h5>SERVICES</h5><ul><li>Lorem Ipsum is</li><li>Lorem Ipsum is simply</li><li>Lorem Ipsum</li><li>Lorem Ipsum is</li><li>Lorem Ipsum is simply</li></ul></div>
    <div><h5>PRODUCTS</h5><ul><li>Lorem Ipsum is</li><li>Lorem Ipsum is simply</li><li>Lorem Ipsum</li><li>Lorem Ipsum is</li><li>Lorem Ipsum is simply</li></ul></div>
    <div><h5>SOFTWARE</h5><ul><li>Lorem Ipsum is</li><li>Lorem Ipsum is simply</li><li>Lorem Ipsum</li><li>Lorem Ipsum is</li><li>Lorem Ipsum is simply</li></ul></div>
    <div><h5>STORE</h5><ul><li>Lorem Ipsum is</li><li>Lorem Ipsum is simply</li><li>Lorem Ipsum</li><li>Lorem Ipsum is</li><li>Lorem Ipsum is simply</li></ul></div>
  </footer>
  <div class="abs copy">© COPYRIGHT 2013 <em>KELVORA MARKET</em>. ALL RIGHTS RESERVED. &nbsp;&nbsp; PRIVACY POLICY &nbsp;| &nbsp;TERMS OF USE</div>

</div>
</body>
</html>
```